Business card for Luxury Portable Restroom Trailer company

We are a Luxury Portable Restroom Trailer Company Called FALCRIDGE HIRES. Based in Orange County California. We provide portable restroom trailers for events, such as, Weddings, Concerts, Charity events, Sporting events, Tournaments, Corporate events, ect. We rent and Sell the Luxury restrooms. Our colors are white, grey, and Orange. As you will see in the logo we uploaded.
There are 2 people in the company so the names and titles will change for the 3 people but card will remain the same. Here is the information for each Person: Dwight Penner CFO 555 318-0476
next Person: Leon Marchetti VP 555 318-0476
Next Person: Owen Marchetti CEO 555 318-0476
Information to include on the card: Luxury Restroom Trailers Rental and Sales. Weddings, Concerts, Charity, Sporting and Corp. Events.

```html
<!DOCTYPE html>
<html lang="en">
<head>
<meta charset="utf-8">
<title>Falcridge Hires – Business Card</title>
<link href="https://fonts.googleapis.com/css2?family=Roboto:wght@400;700;900&display=swap" rel="stylesheet">
<style>
  :root {
    --orange: #e0631f;
    --charcoal: #4a4a4c;
    --grey-text: #3b3b3d;
    --white: #ffffff;
    --stage: #e6e6e8;
  }
  * { box-sizing: border-box; margin: 0; padding: 0; }
  html, body {
    width: 1200px; height: 960px; overflow: hidden;
    background: var(--stage);
    font-family: "Roboto", Arial, sans-serif;
  }
  .canvas {
    position: relative; width: 1200px; height: 960px;
  }
  .card {
    position: absolute; left: 290px;
    width: 620px; height: 355px;
    border-radius: 22px; overflow: hidden;
    box-shadow: 0 10px 28px rgba(0,0,0,.18);
  }
  /* Front face */
  .card-front { top: 95px; background: var(--orange); }
  .front-brand {
    position: absolute; left: 0; right: 0; top: 110px;
    text-align: center;
  }
  .brand-name {
    font-weight: 900; letter-spacing: 1px; text-transform: uppercase;
    color: var(--charcoal); line-height: 1;
  }
  .front-brand .brand-name { font-size: 50px; }
  .front-brand .brand-mark {
    display: inline-block; width: 18px; height: 18px;
    background: var(--charcoal); margin-right: 12px; vertical-align: 6px;
  }
  .tagline {
    position: absolute; left: 0; right: 0; top: 228px;
    text-align: center; color: var(--white);
    font-size: 17px; line-height: 1.35;
  }

  /* Back face */
  .card-back { top: 510px; background: var(--white); }
  .person {
    position: absolute; right: 46px; top: 42px; text-align: right;
  }
  .person-name {
    color: var(--orange); font-weight: 700; font-size: 26px;
    text-transform: uppercase; letter-spacing: .3px;
  }
  .person-title { color: var(--grey-text); font-size: 15px; margin-top: 2px; }
  .edge-tab {
    position: absolute; right: 0; top: 40px;
    width: 18px; height: 52px; background: var(--charcoal);
  }
  .back-brand {
    position: absolute; left: 60px; top: 150px;
  }
  .back-brand .brand-name { font-size: 28px; }
  .back-brand .brand-mark {
    display: inline-block; width: 11px; height: 11px;
    background: var(--orange); margin-right: 8px; vertical-align: 4px;
  }
  .address {
    position: absolute; left: 60px; top: 206px;
    font-size: 16px; line-height: 1.3; color: var(--grey-text);
  }
  .contacts {
    position: absolute; left: 60px; top: 262px; list-style: none;
    font-size: 16px; color: var(--grey-text); line-height: 1.45;
  }
  .contacts li { display: flex; align-items: center; gap: 8px; }
  .contacts svg { width: 13px; height: 13px; fill: var(--orange); flex: none; }
  .edge-bar {
    position: absolute; left: 0; top: 228px;
    width: 16px; height: 127px; background: var(--orange);
  }
</style>
</head>
<body>
<main class="canvas">
  <section class="card card-front" aria-label="Card front">
    <div class="front-brand">
      <span class="brand-mark"></span><span class="brand-name">Falcridge Hires</span>
    </div>
    <p class="tagline">Luxury Restroom Trailers Rental and Sales<br>Weddings, Concerts, Charity, Sporting and Corp Events</p>
  </section>

  <section class="card card-back" aria-label="Card back">
    <div class="edge-tab"></div>
    <div class="person">
      <p class="person-name">Dwight Penner</p>
      <p class="person-title">CFO</p>
    </div>
    <div class="back-brand">
      <span class="brand-mark"></span><span class="brand-name">Falcridge Hires</span>
    </div>
    <p class="address">2710 Harbor View Lane<br>Tustin, CA 92780</p>
    <ul class="contacts">
      <li><svg viewBox="0 0 24 24"><path d="M6.6 10.8a15.1 15.1 0 0 0 6.6 6.6l2.2-2.2a1 1 0 0 1 1-.25 11.4 11.4 0 0 0 3.6.57 1 1 0 0 1 1 1V20a1 1 0 0 1-1 1A17 17 0 0 1 3 4a1 1 0 0 1 1-1h3.5a1 1 0 0 1 1 1c0 1.25.2 2.45.57 3.6a1 1 0 0 1-.25 1z"/></svg>555 318-0476</li>
      <li><svg viewBox="0 0 24 24"><path d="M2 5h20v14H2z M3.5 6.5 12 13l8.5-6.5" stroke="#fff" stroke-width="1.6"/></svg>name@falcridgehires.com</li>
      <li><svg viewBox="0 0 24 24"><circle cx="12" cy="12" r="10"/><path d="M2 12h20M12 2c3 3 3 17 0 20M12 2c-3 3-3 17 0 20" stroke="#fff" stroke-width="1.4" fill="none"/></svg>www.falcridgehires.com</li>
    </ul>
    <div class="edge-bar"></div>
  </section>
</main>
</body>
</html>
```